eBook cover and content: Steering Teams With Quiet Courage

I teach a leadership program to companies that was developed at Varnelo and now need an eBook cover and content design. This downloadable eBook will be offered online in exchange for prospects' contact details. It needs to be designed with a sophisticated, senior HR executive audience in mind. There are some assets that are available for you to work with including photographs, a logo device for the program, and a colour palette (same as Varnelo's blue, green, yellow and red). Note that while the program was developed at Varnelo it is NOT a Varnelo product and I need to ensure that the eBook does not breach license guidelines. I have attached a very rough mockup of the content, images and graphic elements to help.

Target Market(s)

Senior business leaders and HR professionals.

Industry/Entity Type

Leadership

Font styles to use
Sans Serif

Requirements
Must have
• Keep it simple. Clean, contemporary, professional feel. This is a high-value decision for a company and needs to look modern, progressive and credible. Downloadable PDF. Easy to read and digest layout.
• Colours - see attached screenshot for red, blue, green, yellow ref. Additionally charcoal for most type and purple 330033 as extra colour is okay.
• Landscape format please.
Nice to have
• Plenty of white space.

```html
<!DOCTYPE html>
<html lang="en">
<head>
<meta charset="utf-8">
<title>Steering Teams With Quiet Courage – eBook pages</title>
<link rel="stylesheet" href="https://fonts.googleapis.com/css2?family=Montserrat:wght@300;400&family=Raleway:wght@400;500;600&display=swap">
<style>
  :root {
    --canvas: #efefef;
    --paper: #ffffff;
    --charcoal: #3a3a3a;
    --green: #239a55;
    --green-soft: #dcefe2;
    --green-panel: #eef6f0;
    --yellow: #f2b705;
    --purple-deep: #2b1030;
    --purple-glow: #8a3d8f;
    --red: #e0443a;
    --blue: #3b7de0;
  }
  * { box-sizing: border-box; margin: 0; padding: 0; }
  html, body { width: 1200px; height: 851px; overflow: hidden; }
  body {
    background: var(--canvas);
    font-family: "Raleway", sans-serif;
    color: var(--charcoal);
    position: relative;
  }
  .page {
    position: absolute;
    width: 567px;
    height: 395px;
    background: var(--paper);
    box-shadow: 0 1px 3px rgba(0,0,0,.18);
    overflow: hidden;
  }
  .page--autopilot { left: 16px; top: 22px; }
  .page--brain { left: 598px; top: 22px; }
  .page--interesting { left: 16px; top: 435px; }
  .page--how { left: 598px; top: 435px; }

  .brand {
    position: absolute; left: 20px; top: 20px;
    display: flex; align-items: center; gap: 5px;
    font-size: 7px; font-weight: 500; color: var(--charcoal);
  }
  .brand__dot { width: 7px; height: 7px; border-radius: 50%; background: var(--green); }

  .chapter {
    position: absolute; left: 21px; top: 59px; width: 172px;
    display: flex; gap: 4px; align-items: flex-start;
    font-family: "Montserrat", sans-serif; font-weight: 300;
    font-size: 13.4px; line-height: 17px; color: var(--green);
    white-space: nowrap;
  }
  .chapter__num {
    flex: none; width: 18px; height: 18px; border-radius: 50%;
    background: var(--green-soft); color: var(--green);
    display: flex; align-items: center; justify-content: center;
    font-size: 12.5px;
  }
  .chapter__title { padding-top: 0; }

  .copy {
    position: absolute; left: 199px; width: 342px;
    font-size: 8.2px; line-height: 10.4px;
  }
  .copy p { margin-bottom: 5.5px; }
  .copy .lead { color: var(--green); }
  .copy .gap { margin-top: 9px; }

  .folio {
    position: absolute; right: 0; bottom: 12px;
    display: flex; align-items: center; gap: 4px;
    font-size: 7px; color: var(--green);
  }
  .folio::after { content: ""; width: 5px; height: 12px; background: var(--green); }

  .brain-panel {
    position: absolute; left: 199px; top: 211px; width: 342px; height: 75px;
    background: var(--green-panel);
  }
  .brain-panel__art {
    position: absolute; left: 148px; top: 8px; width: 56px; height: 42px;
    border-radius: 50%;
    background: radial-gradient(circle at 45% 45%, #c96a4f, #8f4a3b 60%, #5f7f9c);
  }
  .brain-panel__label {
    position: absolute; font-size: 4.6px; color: var(--green); white-space: nowrap;
  }
  .brain-panel__caption {
    position: absolute; left: 0; right: 0; bottom: 6px;
    text-align: center; font-size: 4.6px; color: var(--green);
  }
  .brain-panel svg { position: absolute; inset: 0; }

  .leadership-diagram { position: absolute; left: 199px; top: 238px; }

  .how__photo {
    position: absolute; inset: 0;
    background:
      radial-gradient(ellipse at 48% 10%, #b06ab5 0%, transparent 45%),
      radial-gradient(ellipse at 42% 62%, #7a4a3e 0%, transparent 40%),
      linear-gradient(160deg, var(--purple-glow) 0%, #4a2148 45%, var(--purple-deep) 100%);
  }
  .how__title {
    position: absolute; left: 19px; top: 64px;
    font-family: "Montserrat", sans-serif; font-weight: 300;
    font-size: 19px; letter-spacing: .5px; color: var(--yellow);
  }
  .how__rule {
    position: absolute; left: 19px; top: 88px; width: 60px; height: 2px; background: var(--yellow);
  }
</style>
</head>
<body>

<section class="page page--autopilot">
  <div class="brand"><span class="brand__dot"></span>Inner Compass</div>
  <h2 class="chapter"><span class="chapter__num">1</span><span class="chapter__title">Getting off autopilot</span></h2>
  <div class="copy" style="top:62px">
    <p>We’re all running on autopilot</p>
    <p>You know what I mean. Days, weeks, sometimes even months go by and we haven’t been present or paying attention. Have you ever driven somewhere only to arrive and not remember how you actually got there? Or been five pages into a book and not remembered a word?</p>
    <p>Running on autopilot has become the new normal for many of us.</p>
    <p class="gap">This is what it feels like:</p>
    <p><span class="lead">Your attention is in the past or future.</span> You’re ruminating about things that have already happened, or your worrying about things that might happen. Either way, you’re not present</p>
    <p><span class="lead">You’re distracted.</span> Easily and all the time. Probably more often than a Goldfish.</p>
    <p><span class="lead">You’re reactive or judgmental.</span> Instead of accepting situations as they are and working with them, you’re getting caught up in your head. You lose connection with who you are, who you’re with and what you’re doing</p>
    <p><span class="lead">You’re acting based on habits, patterns and assumptions.</span> We often default to old ways of thinking and behaviours, and typical ways of reacting. But wouldn’t it be better to have an open mind and consider your responses more deeply?</p>
    <p class="gap">So the first and most important challenge for leadership development is to help people get off autopilot, and stay off.</p>
  </div>
  <div class="folio">3</div>
</section>

<section class="page page--brain">
  <div class="brand"><span class="brand__dot"></span>Inner Compass</div>
  <h2 class="chapter"><span class="chapter__num">3</span><span class="chapter__title">Changing your mind<br>to change your brain</span></h2>
  <div class="copy" style="top:61px">
    <p>Emotional intelligence is what separates star performers from the also rans. It’s also the stuff of outstanding leadership. And wellbeing. Especially now.</p>
    <p>But most people think that their EQ is fixed, like those funny toes you got from your parents.</p>
    <p>What they don’t realise that your brain is ‘plastic’ and can be rewired and reshaped, until you’re at least 90. So you’ve got time.</p>
    <p>Just make sure you’re changing your brain in ways that will be helpful for this crazy-busy world of ours.</p>
    <p>You’ll need to switch off the Default Mode Network of your brain. Not easy when you have so much going on in there. In default mode our brain is lit up like a Christmas tree. You don’t need any more lights and baubles, you need less.</p>
  </div>
  <div class="brain-panel">
    <div class="brain-panel__art" role="img" aria-label="Illustration of the brain with the default mode network regions highlighted"></div>
    <svg width="342" height="75" aria-hidden="true">
      <g stroke="#9fcfae" stroke-width=".5">
        <line x1="122" y1="12" x2="152" y2="12"/>
        <line x1="112" y1="26" x2="150" y2="26"/>
        <line x1="200" y1="20" x2="222" y2="20"/>
        <line x1="202" y1="30" x2="232" y2="30"/>
        <line x1="198" y1="40" x2="222" y2="40"/>
      </g>
    </svg>
    <span class="brain-panel__label" style="left:97px;top:9px">Precuneus</span>
    <span class="brain-panel__label" style="left:38px;top:23px">Posterior inferior parietal region</span>
    <span class="brain-panel__label" style="left:224px;top:17px">Posterior cingulate cortex</span>
    <span class="brain-panel__label" style="left:234px;top:27px">Medial prefrontal cortex</span>
    <span class="brain-panel__label" style="left:224px;top:37px">Lateral temporal cortex</span>
    <p class="brain-panel__caption">Your brain with the Default Mode Network ‘On’. Halden et al 2011, image from Moreau et al 2014</p>
  </div>
  <div class="copy" style="top:299px">
    <p>Leadership programs need to be helping you rewire your brain for calm and clarity, and to help make you more agile, more adaptable and more open and available for critical thinking, collaboration, creativity and problem solving.</p>
    <p>Because they’re the skills you need to lead and contribute at your best.</p>
  </div>
  <div class="folio">5</div>
</section>

<section class="page page--interesting">
  <div class="brand"><span class="brand__dot"></span>Inner Compass</div>
  <h2 class="chapter"><span class="chapter__num">2</span><span class="chapter__title">Learning to lead in<br>interesting times</span></h2>
  <div class="copy" style="top:62px">
    <p>“May you live in interesting times” is known as the “Chinese Curse”. It’s a curse because “interesting” is a proxy for change, chaos and conflict.</p>
    <p>Like it or not, we’re all living in interesting times.</p>
    <p>Command and control. Carrots and sticks. Not much about “top down” leadership models work now, if they ever did. You need new skills to adapt and thrive.</p>
    <p>High-performing companies are flatter, faster, and more agile than their predecessors.</p>
    <p>So you’ll need a different model for leadership. It’s no longer about exercising your authority, it’s about developing your influence.</p>
    <p>Think about that for a moment.</p>
    <p class="gap">Your influence is determined by the way you behave. Your behaviour is tied directly to your emotional intelligence. Which means building new leadership ‘muscles’ starts with training your peoples’ EQ.</p>
  </div>
  <svg class="leadership-diagram" width="342" height="60" aria-label="Traditional top-down pyramid compared with transformational inside-out circles" role="img">
    <text x="6" y="10" font-size="6" fill="#239a55" font-family="Raleway, sans-serif">Traditional leadership</text>
    <text x="6" y="18" font-size="6" fill="#239a55" font-family="Raleway, sans-serif">“Top down”</text>
    <polygon points="107,6 70,58 144,58" fill="#dcefe2" stroke="#9fcfae" stroke-width=".6"/>
    <line x1="94" y1="24" x2="120" y2="24" stroke="#fff"/>
    <line x1="83" y1="40" x2="131" y2="40" stroke="#fff"/>
    <text x="107" y="20" font-size="4.5" text-anchor="middle" fill="#3a3a3a" font-family="Raleway, sans-serif">CEO</text>
    <text x="107" y="35" font-size="4.5" text-anchor="middle" fill="#3a3a3a" font-family="Raleway, sans-serif">Management</text>
    <text x="107" y="52" font-size="4.5" text-anchor="middle" fill="#3a3a3a" font-family="Raleway, sans-serif">Minions</text>
    <text x="161" y="10" font-size="6" fill="#239a55" font-family="Raleway, sans-serif">Transformational</text>
    <text x="161" y="18" font-size="6" fill="#239a55" font-family="Raleway, sans-serif">leadership “Inside out”</text>
    <g stroke="#b8dcc3" stroke-width=".6">
      <line x1="286" y1="0" x2="286" y2="60"/>
      <line x1="250" y1="30" x2="322" y2="30"/>
    </g>
    <circle cx="286" cy="30" r="27" fill="#e6f3ea"/>
    <circle cx="286" cy="30" r="18" fill="#cfe8d7"/>
    <circle cx="286" cy="30" r="9" fill="#b5dcc1"/>
    <text x="286" y="10" font-size="4.5" text-anchor="middle" fill="#3a3a3a" font-family="Raleway, sans-serif">Influence</text>
    <text x="286" y="20" font-size="4.5" text-anchor="middle" fill="#3a3a3a" font-family="Raleway, sans-serif">Behaviour</text>
    <text x="286" y="32" font-size="4.5" text-anchor="middle" fill="#3a3a3a" font-family="Raleway, sans-serif">EQ</text>
  </svg>
  <div class="copy" style="top:308px">
    <p>Make sure leadership training provides your people with a leadership model for now, and the skills they need to muscle-up on emotional intelligence.</p>
    <p>And now, to number three.</p>
  </div>
  <div class="folio">4</div>
</section>

<section class="page page--how">
  <div class="how__photo" role="img" aria-label="Photograph of smiling participants at a leadership workshop under warm purple light"></div>
  <h2 class="how__title">HOW IT WORKS</h2>
  <div class="how__rule"></div>
</section>

</body>
</html>
```